Renewed Website Design for B2B Company

We need a renewed design for Van Roost - an international trading company in raw materials: natural oils (essential oils, fatty oils, and extracts) and related products such as aromas, fragrances, etc.

Page designs to create:

1. Home page (see the mockup, the content and structure should be exactly like this, however feel free creative-wise)

2. Products page(includes all the 11 product categories which you see on van-roost.nl and some small description of them).

Current website: van-roost.nl
Competitors' websites: brivelmaroilworks.com & qtuvx.com (they don't have particularly perfect websites design-wise, however, it's mostly to give you the idea of this market).

Please, go to this Google Drive folder - https://kortlink.example/7TxwPq - to see Van Roost's logo in different variations, brandbook with colors, fonts, and a brochure with 'mood board' pictures.

Target Market(s)

B2B companies needing white label products like natural/essential/fatty oils, fragrances etc.

Number of Pages Required

2 page

Font styles to use
Other font styles liked:
• Open Sans

Colors

Designer to choose colors to be used in the design.

Requirements
Should not have
• No images with people; no turqoise, blue or pink colors; no overlays over pictures

```html
<!DOCTYPE html>
<html lang="nl">
<head>
<meta charset="utf-8">
<title>Van Roost – Uw betrouwbare sourcingpartner</title>
<link href="https://fonts.googleapis.com/css2?family=Montserrat:wght@700;800&family=Open+Sans:wght@400;600;700&display=swap" rel="stylesheet">
<style>
:root{
  --green:#0b5a2b;
  --green-dark:#08491f;
  --red:#e1101d;
  --text:#444;
  --muted:#7a7a7a;
  --line:#8fae98;
  --white:#fff;
  --blush:#f7f1ef;
}
*{box-sizing:border-box;margin:0;padding:0}
html,body{width:1200px;height:3292px;overflow:hidden;background:var(--white)}
body{position:relative;font-family:"Open Sans",sans-serif;color:var(--text)}
.abs{position:absolute}
.heading{font-family:"Montserrat",sans-serif;font-weight:800;color:var(--green);text-transform:uppercase;text-align:center}
.heading::after{content:"";display:block;width:74px;height:4px;background:var(--red);margin:10px auto 0}
.btn{position:absolute;background:var(--red);color:var(--white);font-family:"Open Sans",sans-serif;font-weight:700;font-size:14px;border-radius:26px;height:48px;line-height:48px;padding:0 25px;text-transform:uppercase;letter-spacing:.2px}

/* header */
.site-header{top:0;left:0;width:1200px;height:104px;border-bottom:4px solid var(--green)}
.brand{position:absolute;display:flex;align-items:center;gap:12px}
.brand-dot{width:44px;height:44px;border-radius:50%;background:var(--green)}
.brand-name{font-family:"Montserrat",sans-serif;font-weight:800;color:var(--red);font-size:38px;letter-spacing:.5px}
.nav{position:absolute;left:427px;top:46px;display:flex;gap:25px;font-size:13.5px;font-weight:600;color:#222}
.lang{position:absolute;top:35px;width:40px;height:40px;border-radius:50%;font-size:12px;font-weight:700;text-align:center;line-height:40px;box-shadow:0 2px 6px rgba(0,0,0,.15)}

/* hero */
.hero{top:104px;left:0;width:1200px;height:670px}
.hero-title{position:absolute;left:560px;top:215px;width:530px;text-align:right;font-family:"Montserrat",sans-serif;font-weight:800;font-size:47px;line-height:58px;color:var(--white);text-transform:uppercase}
.hero-title .outline{color:transparent;-webkit-text-stroke:1.5px var(--white);display:block}
.hero-social{position:absolute;left:1125px;width:38px;height:38px;border-radius:50%}

/* products */
.card{position:absolute;top:910px;width:308px;height:566px;border-radius:154px;background:var(--white);box-shadow:0 6px 22px rgba(0,0,0,.09);text-align:center}
.card-img{position:absolute;left:17px;top:17px;width:274px;height:274px;border-radius:50%}
.card h3{position:absolute;top:316px;left:0;width:100%;font-size:19px;font-weight:600;color:#2b2b2b;text-transform:uppercase;letter-spacing:.3px}
.card h3::after{content:"";display:block;width:46px;height:3px;background:var(--line);margin:9px auto 0}
.card p{position:absolute;top:360px;left:20px;width:268px;font-size:13.8px;line-height:25px;color:var(--muted)}

.intro{left:150px;top:1596px;width:900px;text-align:center;font-size:20.5px;line-height:32px;color:#555}

/* over ons */
.about-text p{font-size:14px;line-height:25.6px;color:var(--muted);text-align:justify;margin-bottom:15px}
.about-text a{color:var(--red);font-weight:700}

/* werkwijze */
.method{top:2492px;left:0;width:1200px;height:537px;background:var(--green)}
.method h2{position:absolute;left:112px;top:124px;font-family:"Montserrat",sans-serif;font-weight:800;font-size:38px;color:var(--white);text-transform:uppercase}
.method h2::after{content:"";display:block;width:74px;height:4px;background:var(--white);margin-top:10px}
.method-text{position:absolute;left:112px;top:216px;width:478px}
.method-text p{font-size:14px;line-height:25.6px;color:#eef3ef;text-align:justify;margin-bottom:9px}
.frame{position:absolute;border:6px solid var(--white)}

/* footer */
.footer-info{right:112px;text-align:right;font-size:15.5px;color:#333;display:flex;align-items:center;gap:10px;justify-content:flex-end}
.badge{width:36px;height:28px;border-radius:50%;background:#d6dde6}
.f-social{position:absolute;top:3231px;width:38px;height:38px;border-radius:50%;background:var(--white);box-shadow:0 2px 8px rgba(0,0,0,.15)}
</style>
</head>
<body>

<header class="abs site-header">
  <div class="brand" style="left:112px;top:31px">
    <span class="brand-dot"></span><span class="brand-name">VAN ROOST</span>
  </div>
  <nav class="nav">
    <span>PRODUCTEN</span><span>TEAM</span><span>WERKWIJZE</span><span>CERTIFICERINGEN</span><span>CONTACT</span><span style="font-weight:400">|</span>
    <svg width="14" height="14" viewBox="0 0 14 14" style="margin-top:2px"><circle cx="6" cy="6" r="4.2" fill="none" stroke="#222" stroke-width="1.8"/><line x1="9" y1="9" x2="12.5" y2="12.5" stroke="#222" stroke-width="2"/></svg>
  </nav>
  <span class="lang" style="left:1004px;background:var(--red);color:var(--white)">NL</span>
  <span class="lang" style="left:1049px;background:var(--white);color:var(--red)">EN</span>
</header>

<section class="abs hero">
  <svg class="abs" style="left:0;top:0" width="1200" height="670" viewBox="0 0 1200 670">
    <defs>
      <linearGradient id="heroPhoto" x1="0" y1="0" x2="1" y2="1">
        <stop offset="0" stop-color="#c9cdc6"/>
        <stop offset=".45" stop-color="#a89a7c"/>
        <stop offset=".7" stop-color="#8a5a22"/>
        <stop offset="1" stop-color="#5d7650"/>
      </linearGradient>
    </defs>
    <path d="M0,530 C150,660 360,670 545,585 L655,585 C840,670 1050,660 1200,530 V0 H0 Z" fill="var(--green)" transform="translate(0,12)"/>
    <path d="M0,530 C150,660 360,670 545,585 L655,585 C840,670 1050,660 1200,530 V0 H0 Z" fill="url(#heroPhoto)" role="img" aria-label="Foto: etherische olie in amberkleurig flesje met pipet, vijzel en eucalyptusbladeren"/>
    <circle cx="600" cy="536" r="57" fill="none" stroke="var(--white)" stroke-width="2"/>
    <circle cx="600" cy="541" r="45" fill="var(--white)"/>
    <path d="M591,531 l9,8 l9,-8 M591,541 l9,8 l9,-8" fill="none" stroke="#222" stroke-width="2.4"/>
  </svg>
  <h1 class="hero-title">Uw betrouwbare<span class="outline">sourcingpartner</span></h1>
  <span class="btn" style="left:591px;top:355px">Naar producten</span>
  <span class="hero-social" style="top:221px;border:1.5px solid var(--white)"></span>
  <svg class="abs" style="left:1138px;top:270px" width="12" height="100"><circle cx="6" cy="6" r="4" fill="var(--white)"/><circle cx="6" cy="46" r="4" fill="var(--white)"/><circle cx="6" cy="85" r="4" fill="var(--white)"/></svg>
</section>

<!-- light background behind products & intro -->
<svg class="abs" style="left:0;top:1300px" width="1200" height="594" viewBox="0 0 1200 594">
  <defs><linearGradient id="blush" x1="0" y1="0" x2="0" y2="1"><stop offset="0" stop-color="var(--blush)"/><stop offset="1" stop-color="#fbf8f7"/></linearGradient></defs>
  <path d="M0,140 Q600,-100 1200,140 V594 H0 Z" fill="url(#blush)"/>
</svg>

<h2 class="abs heading" style="left:0;top:815px;width:1200px;font-size:38px">Producten</h2>

<article class="card" style="left:112px">
  <div class="card-img" role="img" aria-label="Foto: olieflesjes met verse kruiden en bloemen" style="background:radial-gradient(circle at 55% 45%,#9a8a2a,#5e4a22 60%,#3a2a18)"></div>
  <h3>Natuurlijk oliën</h3>
  <p>Keuze uit een uitgebreid assortiment uit voorraad leverbare etherische en vette oliën. Niet op voorraad? Geen probleem! Door onze ruime ervaring en wereldwijde netwerk is nauwelijks een natuurlijke olie die wij niet kunnen leveren.</p>
</article>
<article class="card" style="left:446px">
  <div class="card-img" role="img" aria-label="Foto: parfumflesje met lavendel en badzout" style="background:radial-gradient(circle at 50% 50%,#9d8bc6,#6c7fa0 55%,#4f8b8e)"></div>
  <h3>Parfums en aroma’s</h3>
  <p>Geur- en smaakstoffen onder de merknaam Aromelle. Onze specialisten ontwikkelen eigen parfum compounds en flavour compounds voor elke toepassing. De mogelijkheden zijn eindeloos.</p>
</article>
<article class="card" style="left:780px">
  <div class="card-img" role="img" aria-label="Foto: bloem met vanillestokjes op papier" style="background:radial-gradient(circle at 50% 40%,#f0ddc8,#d9a98a 60%,#b88466)"></div>
  <h3>Grondstoffen</h3>
  <p>Ingrediënten en halffabricaten die afgeleid zijn van of veel gebruikt worden met natuurlijke oliën. Voor veel producerende bedrijven zijn wij daarmee een one-stop-shop partner.</p>
</article>

<h2 class="abs heading" style="left:0;top:1515px;width:1200px;font-size:38px">Wat doen we?</h2>
<p class="abs intro">Van Roost is een solide en betrouwbare leverancier van grondstoffen voor de cosmetische-, chemische, reform-, feed- en foodsector. Wij onderscheiden ons door een hoog serviceniveau en uitgebreid aanbod.</p>
<div class="abs" role="img" aria-label="Foto: natuurlijke ingrediënten, dennenappels, vijzel, capsules en olieflesjes op een rij" style="left:0;top:1690px;width:1200px;height:204px;background:linear-gradient(180deg,rgba(247,241,239,0) 0%,#e9ddd3 45%,#d9c2aa 100%)"></div>
<span class="btn" style="left:508px;top:1732px">Naar producten</span>

<!-- over ons -->
<div class="abs" role="img" aria-label="Foto: kaars, olieflesjes, stenen en handdoek in spa-opstelling" style="left:112px;top:2000px;width:488px;height:368px;background:linear-gradient(135deg,#dfe0dc,#b8bbb2 45%,#6c7a4e 70%,#3a3a36)"></div>
<h2 class="abs heading" style="left:679px;top:2052px;font-size:38px;text-align:left">Over ons</h2>
<style>.about-h::after{}</style>
<div class="abs about-text" style="left:679px;top:2145px;width:410px">
  <p>Dit zijn wij, een groeiend familiebedrijf in Tegelen (Venlo) dat werkt met een professioneel en hecht team <a>beeld</a>. Wij vinden het van groot belang dat onze klanten tevreden zijn, daarom proberen wij altijd net dat stapje extra te zetten.</p>
  <p>Van Roost (anno 1979) bestaat ruim 40 jaar. Wil je meer weten over het verhaal achter Van Roost? Klik dan hier <a>klik</a>.</p>
</div>

<!-- werkwijze -->
<section class="abs method">
  <h2>Werkwijze</h2>
  <div class="method-text">
    <p>Wij leveren grondstoffen uit voorraad , standaard verpakt in IBC’s, vaten of jerrycans, maar ook levering in kleinere verpakkingen zijn bij ons mogelijk. De producten worden (zo dicht mogelijk) bij de bron aangekocht of zelf ontwikkeld. Hierdoor en dankzij ons eigen kwaliteitssysteem is de juiste kwaliteit gegarandeerd.</p>
    <p>Door de directe lijnen zijn wij in staat tot snelle en flexibele levering tegen scherpe prijzen. Hebben we een product niet in ons assortiment dan gaan we op zoek en vinden we een passende oplossing.</p>
  </div>
  <div class="frame" role="img" aria-label="Foto: lavendel met flesje olie" style="left:715px;top:108px;width:374px;height:297px;background:linear-gradient(120deg,#8b7ab8,#c9c3cf 50%,#e3c25a 80%,#f1ede6)"></div>
  <div class="frame" role="img" aria-label="Foto: olieflesjes met bloemen" style="left:667px;top:298px;width:194px;height:152px;background:linear-gradient(135deg,#c9bfa8,#7a5a32 55%,#3d3a2a)"></div>
</section>

<!-- footer -->
<footer>
  <div class="abs" style="left:112px;top:3093px;width:195px;text-align:center">
    <span style="display:block;width:42px;height:42px;border-radius:50%;background:var(--green);margin:0 auto 14px"></span>
    <span class="brand-name" style="font-size:36px;white-space:nowrap">VAN ROOST</span>
  </div>
  <div class="abs footer-info" style="top:3089px">
    <svg width="11" height="15" viewBox="0 0 11 15"><path d="M5.5,0 C2.5,0 0,2.4 0,5.4 C0,9.2 5.5,15 5.5,15 S11,9.2 11,5.4 C11,2.4 8.5,0 5.5,0Z" fill="var(--red)"/><circle cx="5.5" cy="5.3" r="2" fill="var(--white)"/></svg>
    <span>Lindenweg 12, 5912 KR lever: Tegelen (Venlo 7712) – The Netherlands</span>
  </div>
  <div class="abs footer-info" style="top:3127px">
    <svg width="14" height="14" viewBox="0 0 14 14"><path d="M3,0 L5.5,3.5 L4,5.3 C5,7.5 6.5,9 8.7,10 L10.5,8.5 L14,11 L12.3,13.7 C6,13.5 0.5,8 0.3,1.7 Z" fill="var(--red)"/></svg>
    <span>+31 (0)77-4820315</span><span style="margin:0 14px">|</span>
    <svg width="16" height="12" viewBox="0 0 16 12"><rect width="16" height="12" rx="1.5" fill="var(--red)"/><path d="M1,1.5 L8,7 L15,1.5" fill="none" stroke="var(--white)" stroke-width="1.4"/></svg>
    <span>hallo@van-roost.nl</span>
  </div>
  <div class="abs footer-info" style="top:3164px;gap:17px">
    <span class="badge" style="background:#cfe3cf"></span><span class="badge"></span><span class="badge"></span><span class="badge"></span><span class="badge" style="width:52px;border-radius:4px;background:#d9d9d9"></span>
  </div>
  <div class="abs" style="left:112px;top:3226px;width:976px;height:1px;background:#ddd"></div>
  <p class="abs" style="left:0;top:3243px;width:1200px;text-align:center;font-size:13px;color:#444">© 2022 VAN ROOST &nbsp;|&nbsp; Alle rechten voorbehouden</p>
  <span class="f-social" style="left:922px;background:var(--red)"></span>
  <span class="f-social" style="left:964px"></span>
  <span class="f-social" style="left:1007px"></span>
  <span class="f-social" style="left:1050px"></span>
</footer>

</body>
</html>
```